The Linen Loft Co

We need a business card design for our wardrobe company.
Please visit our website www.gentlelinenlofts.com to get an idea of who we are.

```html
<!DOCTYPE html>
<html lang="en">
<head>
<meta charset="utf-8">
<title>The Linen Loft Co — Business Card</title>
<link rel="stylesheet" href="https://fonts.googleapis.com/css2?family=Lato:wght@400;700&family=PT+Sans:wght@400&family=Roboto:wght@700&display=swap">
<style>
  :root {
    --stage: #1e1e1e;
    --card: #ffffff;
    --gold: #97805a;
    --ink: #111111;
    --slate: #3e3e44;
    --body: #333338;
  }
  * { margin: 0; padding: 0; box-sizing: border-box; }
  html, body {
    width: 1200px;
    height: 900px;
    overflow: hidden;
    background: var(--stage);
  }
  .card {
    position: absolute;
    left: 100px;
    top: 165px;
    width: 1000px;
    height: 570px;
    background: var(--card);
    border-radius: 36px;
    overflow: hidden;
  }
  .card__band {
    position: absolute;
    left: 0;
    bottom: 0;
    width: 100%;
    height: 25px;
    background: var(--gold);
  }
  .brand {
    position: absolute;
    right: 54px;
    top: 97px;
    display: flex;
    align-items: center;
    gap: 14px;
  }
  .brand__mark {
    width: 66px;
    height: 66px;
    background: var(--gold);
  }
  .brand__text {
    text-align: center;
  }
  .brand__name {
    font-family: "Lato", sans-serif;
    font-weight: 700;
    font-size: 21px;
    letter-spacing: 1.4px;
    color: var(--ink);
    text-transform: uppercase;
  }
  .brand__tagline {
    margin-top: 7px;
    font-family: "Lato", sans-serif;
    font-weight: 700;
    font-size: 17px;
    color: var(--ink);
  }
  .person {
    position: absolute;
    left: 52px;
    top: 273px;
  }
  .person__name {
    font-family: "Roboto", sans-serif;
    font-weight: 700;
    font-size: 42px;
    line-height: 1;
    color: var(--gold);
  }
  .person__role {
    margin-top: 10px;
    font-family: "PT Sans", sans-serif;
    font-size: 35px;
    line-height: 1;
    color: var(--slate);
  }
  .divider {
    position: absolute;
    left: 52px;
    top: 385px;
    width: 16px;
    height: 5px;
    background: var(--gold);
  }
  .contacts {
    position: absolute;
    left: 52px;
    top: 408px;
    list-style: none;
  }
  .contacts__item {
    display: flex;
    align-items: center;
    gap: 9px;
    height: 30px;
    font-family: "Lato", sans-serif;
    font-size: 22px;
    letter-spacing: 0.6px;
    color: var(--body);
  }
  .contacts__icon {
    width: 17px;
    height: 17px;
    flex: none;
  }
  .address {
    position: absolute;
    right: 54px;
    top: 469px;
    text-align: right;
    font-family: "Lato", sans-serif;
    font-size: 22px;
    line-height: 30px;
    letter-spacing: 1.6px;
    color: var(--body);
    font-style: normal;
  }
</style>
</head>
<body>
  <main class="card">
    <header class="brand">
      <div class="brand__mark"></div>
      <div class="brand__text">
        <p class="brand__name">The Linen Loft Co</p>
        <p class="brand__tagline">Made to Fit Every Room</p>
      </div>
    </header>

    <section class="person">
      <h1 class="person__name">Daren Holt</h1>
      <p class="person__role">Manager</p>
    </section>

    <div class="divider"></div>

    <ul class="contacts">
      <li class="contacts__item">
        <svg class="contacts__icon" viewBox="0 0 24 24" aria-hidden="true"><path fill="#97805a" d="M6.6 10.8a15.1 15.1 0 0 0 6.6 6.6l2.2-2.2a1 1 0 0 1 1-.25 11.4 11.4 0 0 0 3.6.57 1 1 0 0 1 1 1V20a1 1 0 0 1-1 1A17 17 0 0 1 3 4a1 1 0 0 1 1-1h3.5a1 1 0 0 1 1 1c0 1.250.2 2.45.57 3.57a1 1 0 0 1-.25 1z"/></svg>
        <span>403-555-0148</span>
      </li>
      <li class="contacts__item">
        <svg class="contacts__icon" viewBox="0 0 24 24" aria-hidden="true"><rect x="6.5" y="2" width="11" height="20" rx="2" fill="none" stroke="#97805a" stroke-width="2"/><circle cx="12" cy="18.5" r="1" fill="#97805a"/></svg>
        <span>403-555-0192</span>
      </li>
      <li class="contacts__item">
        <svg class="contacts__icon" viewBox="0 0 24 24" aria-hidden="true"><rect x="2" y="5" width="20" height="14" rx="1" fill="#97805a"/><path d="M3.5 6.5 12 13l8.5-6.5" fill="none" stroke="#fff" stroke-width="1.8"/></svg>
        <span>info@gentlelinenlofts.com</span>
      </li>
      <li class="contacts__item">
        <svg class="contacts__icon" viewBox="0 0 24 24" aria-hidden="true"><circle cx="12" cy="12" r="10" fill="#97805a"/><path d="M7 6.5c2 .5 2.5 2 2 3.5s-2.5 1.5-3 3.5M14 4.5c-1 1.5 0 3 1.5 3s2.5 1.5 1.5 3-2.5 1-3 3 1 3 2 4.5" fill="none" stroke="#fff" stroke-width="1.6"/></svg>
        <span>www.gentlelinenlofts.com</span>
      </li>
    </ul>

    <address class="address">
      18-20 Marlowe Crescent<br>
      Avenue 550210, USA
    </address>

    <div class="card__band"></div>
  </main>
</body>
</html>
```